Tovel & Associates - London New Letting and Property Management Company *

Tovel & Associates LTD is a new company based in London, and works with brand new residential property in the city centre.

We are aiming to have 1000 new properties a year.

We are looking for something modern and minimalistic :
Logo ,Monogram, Paper Head and Business Card.

Target Market(s)

Internation landlords

Industry/Entity Type

Real Estate

Logo Text

Tovel & Associates

Colors

Designer to choose colors to be used in the design.

Requirements
Nice to have
• A particular monogram with "TA"
Should not have
• Little House over the logo

```html
<!DOCTYPE html>
<html lang="en">
<head>
<meta charset="utf-8">
<title>Tovel &amp; Associates — Stationery</title>
<link href="https://fonts.googleapis.com/css2?family=Raleway:wght@400;500;600&display=swap" rel="stylesheet">
<style>
  :root{
    --bg:#f7f6f4;
    --paper:#ffffff;
    --slate:#37414a;
    --ink:#1a1a1a;
    --text:#2b2f33;
    --rule:#8a8f94;
    --light:#ffffff;
  }
  *{box-sizing:border-box;margin:0;padding:0}
  html,body{width:1200px;height:1200px;overflow:hidden}
  body{background:var(--bg);font-family:"Raleway",sans-serif;color:var(--text);position:relative}
  .piece{position:absolute;box-shadow:3px 4px 8px rgba(0,0,0,.18)}
  .wordmark{font-family:"Raleway",sans-serif;font-weight:600;white-space:nowrap;letter-spacing:.02em}
  .caption{position:absolute;font-size:5px;letter-spacing:.08em;color:#555;transform:rotate(-90deg);transform-origin:left top;white-space:nowrap}
  .caption::before{content:"";display:inline-block;width:3px;height:5px;background:var(--slate);margin-right:3px;vertical-align:-1px}

  .logo-card{width:388px;height:149px;left:195px;display:flex;align-items:center;justify-content:center}
  .logo-card .wordmark{font-size:26px}
  .logo-card--white{top:20px;background:var(--paper);color:var(--slate)}
  .logo-card--white .wordmark{font-size:17px}
  .logo-card--slate{top:178px;background:var(--slate);color:var(--light)}
  .logo-card--black{top:337px;background:var(--ink);color:var(--light)}

  .card-back{left:692px;top:46px;width:278px;height:158px;background:var(--slate);color:var(--light);display:flex;align-items:center;justify-content:center}
  .card-back .wordmark{font-size:20px}

  .card-front{left:800px;top:311px;width:278px;height:159px;background:var(--slate);color:var(--light);overflow:hidden}
  .card-front .vline{position:absolute;top:0;bottom:0;width:1px;background:rgba(255,255,255,.7)}
  .card-front .hline{position:absolute;left:0;right:0;top:111px;height:1px;background:rgba(255,255,255,.7)}
  .card-front .wordmark{position:absolute;left:12px;top:14px;font-size:8px}
  .card-front .name{position:absolute;left:149px;top:82px;font-size:10px;font-weight:600;letter-spacing:.06em}
  .card-front .role{position:absolute;left:149px;top:96px;font-size:7px;opacity:.85}
  .card-front .info{position:absolute;left:149px;font-size:6px;opacity:.9}
  .card-front .web{position:absolute;left:14px;top:144px;font-size:6.5px;opacity:.9}

  .sheet{top:531px;width:439px;height:635px;background:var(--paper)}
  .sheet .vline{position:absolute;top:0;bottom:0;width:1px;background:var(--rule)}
  .sheet .hline{position:absolute;left:0;right:0;top:111px;height:1px;background:var(--rule)}
  .sheet--blank{left:170px}
  .sheet--blank .wordmark{position:absolute;left:30px;top:462px;font-size:44px;line-height:1.08;color:var(--slate)}
  .sheet--letter{left:662px}
  .sheet--letter .wordmark{position:absolute;left:10px;top:40px;font-size:13px;line-height:1.15;color:var(--slate)}
  .contact{position:absolute;left:310px;display:flex;align-items:center;gap:6px;font-size:6.5px;color:#555}
  .contact svg{width:9px;height:9px}
  .date{position:absolute;right:40px;top:128px;font-size:8.5px;letter-spacing:.03em}
  .letter-body{position:absolute;left:128px;top:217px;width:290px;font-size:8.6px;line-height:10.5px;letter-spacing:.02em}
  .letter-body p{margin-bottom:10.5px}
  .signature{display:block;width:48px;height:12px;margin:16px 0 3px 4px;background:linear-gradient(90deg,#d8d8d8,#efefef)}
  .signer{font-weight:600;font-size:8.6px;margin-left:4px}
  .signer-role{font-size:7.6px;margin-left:4px}
  .footer-web{position:absolute;left:16px;top:618px;display:flex;align-items:center;gap:6px;font-size:7px;color:#555}
  .footer-band{position:absolute;left:233px;bottom:0;width:206px;height:16px;background:var(--slate)}
</style>
</head>
<body>

  <span class="caption" style="left:166px;top:486px">MONOGRAM LOGO DESIGNS</span>
  <div class="piece logo-card logo-card--white"><span class="wordmark">Tovel &amp; Associates</span></div>
  <div class="piece logo-card logo-card--slate"><span class="wordmark">Tovel &amp; Associates</span></div>
  <div class="piece logo-card logo-card--black"><span class="wordmark">Tovel &amp; Associates</span></div>

  <span class="caption" style="left:666px;top:208px">BUSINESS CARD BACK</span>
  <div class="piece card-back"><span class="wordmark">Tovel &amp; Associates</span></div>

  <span class="caption" style="left:776px;top:470px">BUSINESS CARD FRONT</span>
  <div class="piece card-front">
    <span class="vline" style="left:98px"></span>
    <span class="vline" style="left:142px"></span>
    <span class="hline"></span>
    <span class="wordmark">Tovel &amp; Associates</span>
    <span class="name">DANE CORROW</span>
    <span class="role">Director</span>
    <span class="info" style="top:117px">+44 (0) 20 7946 0321</span>
    <span class="info" style="top:131px">danecorrow@tovelassociates.co.uk</span>
    <span class="info" style="top:145px">18 Linden Row, London.</span>
    <span class="web">tovelassociates.co.uk</span>
  </div>

  <div class="piece sheet sheet--blank">
    <span class="vline" style="left:329px"></span>
    <span class="hline"></span>
    <span class="wordmark">Tovel &amp;<br>Associates</span>
  </div>

  <div class="piece sheet sheet--letter">
    <span class="vline" style="left:110px"></span>
    <span class="hline"></span>
    <span class="wordmark">Tovel &amp;<br>Associates</span>

    <div class="contact" style="top:54px">
      <svg viewBox="0 0 10 10"><circle cx="5" cy="5" r="5" fill="#37414a"/><path d="M3.3 2.8c.3 1.9 1.6 3.3 3.6 3.9l.4-.8-1-.6-.5.4c-.6-.3-1-.8-1.2-1.4l.4-.5-.6-1z" fill="#fff"/></svg>
      +44 (0) 20 7946 0321
    </div>
    <div class="contact" style="top:67px">
      <svg viewBox="0 0 10 10"><circle cx="5" cy="5" r="5" fill="#37414a"/><rect x="2.7" y="3.4" width="4.6" height="3.2" fill="#fff"/><path d="M2.7 3.4L5 5.2 7.3 3.4" stroke="#37414a" stroke-width=".5" fill="none"/></svg>
      info@tovelassociates.co.uk
    </div>
    <div class="contact" style="top:81px">
      <svg viewBox="0 0 10 10"><circle cx="5" cy="5" r="5" fill="#37414a"/><path d="M5 2.4a1.8 1.8 0 0 1 1.8 1.8C6.8 5.6 5 7.6 5 7.6S3.2 5.6 3.2 4.2A1.8 1.8 0 0 1 5 2.4z" fill="#fff"/></svg>
      18 Linden Row, London.
    </div>

    <div class="date">09 November 2018</div>

    <div class="letter-body">
      <p>Hello Mr Hallam,</p>
      <p>I noticed that you have had your home for sale by owner for 4 weeks and was wondering if I could be of any assistance. I recently sold homes in the neighborhood at Fenwick Street and have active buyers looking in the area.</p>
      <p>I understand that saving on the commission is probably very important to you. I bet you didn't know that homes that sell with a real estate agent get a higher overall price than those that sold without one — often making up for the difference. I am hoping that we could work together, get the right price on your home and get your home sold.</p>
      <p>Call or text me at +44 (0) 20 7946 0321. We'll set up time, and I'm happy to share my ideas and marketing strategy to get your home sold fast.</p>
      <p style="margin-left:2px">Best Regards</p>
      <span class="signature" role="img" aria-label="Handwritten signature"></span>
      <div class="signer">Dane Corrow</div>
      <div class="signer-role">Managing Director, Tovel &amp; Associates LTD</div>
    </div>

    <div class="footer-web">
      <svg width="9" height="9" viewBox="0 0 10 10"><circle cx="5" cy="5" r="5" fill="#37414a"/><circle cx="5" cy="5" r="2.4" fill="none" stroke="#fff" stroke-width=".7"/></svg>
      tovelassociates.co.uk
    </div>
    <span class="footer-band"></span>
  </div>

</body>
</html>
```